Business card design for new eCommerce site focusing on integrity and strong businsess tactics

We need a business card that will stand out and be memorable. Something with color that matches our company logo colors. Think high end version of Pactivo. There are 2 logos provided. The parent company is called Amber Ledge Partners and we are presenting a new and very exciting eCommerce site called BrightHarborTrade.example.

Target Market(s)

Our target markets are in the Activities, Food and Beverage, Health and Beauty

Industry/Entity Type

Marketing

Contact Information for Business Card

We have 4 members that need cards...I will provide all info to the winner of the design contest
Business Address is
4870 West 63rd Avenue, Suite C207
Phoenix AZ 85731

Font styles to use
Serif
Sans Serif

Colors

Designer to choose colors to be used in the design.

Requirements
Must have
• The card must be memorable...should be unique in design but must exude integrity and be playful .
• I have provided several colors or our parent company...please feel free to use which ever
Nice to have
• I will leave this up to you. Feel free to use other images of your choosing that wraps around our client.....Activities, Dining, Health, Beauty
Should not have
• just dont be boring

```html
<!DOCTYPE html>
<html lang="en">
<head>
<meta charset="utf-8">
<title>BrightHarborTrade.example — Business Card</title>
<link href="https://fonts.googleapis.com/css2?family=Questrial&display=swap" rel="stylesheet">
<style>
  :root {
    --bg: #3a3a3c;
    --paper: #f4f5f5;
    --blue: #2a7bb0;
    --green: #6cb33f;
    --ink: #4a4d50;
    --muted: #6d7174;
  }
  html, body {
    margin: 0;
    padding: 0;
    width: 1200px;
    height: 834px;
    overflow: hidden;
    background: var(--bg);
    font-family: "Questrial", "Century Gothic", sans-serif;
  }
  .stage { position: relative; width: 1200px; height: 834px; }
  .card {
    position: absolute;
    width: 620px;
    height: 354px;
    background: var(--paper);
    overflow: hidden;
    box-shadow: 0 10px 28px rgba(0,0,0,.45);
  }
  .card--front { left: 120px; top: 40px; }
  .card--back { left: 460px; top: 440px; }
  .card .wave { position: absolute; inset: 0; width: 100%; height: 100%; }
  .wave .stripe { fill: var(--green); }
  .wave .gap { fill: #ffffff; }
  .wave .band { fill: var(--blue); }

  .brand { position: absolute; display: flex; align-items: center; gap: 12px; }
  .brand__dot { width: 28px; height: 28px; border-radius: 50%; background: var(--blue); flex: none; }
  .brand__name { color: var(--green); font-size: 26px; line-height: 1; letter-spacing: -0.5px; white-space: nowrap; }
  .brand__tagline { color: var(--muted); font-size: 12px; letter-spacing: 1px; margin-top: 6px; white-space: nowrap; }
  .card--front .brand { left: 56px; top: 108px; }
  .card--back .brand { left: 250px; top: 62px; }
  .card--back .brand__name { font-size: 22px; }
  .card--back .brand__dot { width: 22px; height: 22px; }
  .card--back .brand__tagline { font-size: 10px; }

  .partner { position: absolute; right: 40px; top: 26px; text-align: center; }
  .partner__mark { width: 50px; height: 50px; border-radius: 50%; background: var(--green); margin: 0 auto 6px; }
  .partner__name { color: var(--green); font-size: 13px; white-space: nowrap; }

  .contact { position: absolute; left: 56px; top: 150px; color: var(--ink); }
  .contact__name { color: var(--blue); font-size: 17px; font-weight: 700; letter-spacing: .5px; }
  .contact__role { color: var(--green); font-size: 14px; margin: 2px 0 12px; }
  .contact__line { font-size: 11px; line-height: 17px; color: var(--muted); }
  .contact__row { display: flex; align-items: center; gap: 10px; font-size: 11px; line-height: 18px; color: var(--muted); }
  .contact__row:first-of-type { margin-top: 10px; }
  .contact__row svg { width: 12px; height: 12px; stroke: var(--green); fill: none; stroke-width: 1.6; }

  .web { position: absolute; right: 28px; bottom: 22px; color: #ffffff; font-size: 12px; letter-spacing: .5px; white-space: nowrap; }
</style>
</head>
<body>
<main class="stage">

  <section class="card card--front" aria-label="Card front">
    <svg class="wave" viewBox="0 0 620 354" preserveAspectRatio="none" aria-hidden="true">
      <path class="stripe" transform="translate(0,-16)" d="M0,306 C220,306 330,266 430,190 C490,144 550,126 620,122 L620,370 L0,370 Z"/>
      <path class="gap" transform="translate(0,-7)" d="M0,306 C220,306 330,266 430,190 C490,144 550,126 620,122 L620,370 L0,370 Z"/>
      <path class="band" d="M0,306 C220,306 330,266 430,190 C490,144 550,126 620,122 L620,354 L0,354 Z"/>
    </svg>
    <div class="brand">
      <span class="brand__dot"></span>
      <div>
        <div class="brand__name">BrightHarborTrade.example</div>
        <div class="brand__tagline">Activities-Dining-Health-Beauty</div>
      </div>
    </div>
    <div class="partner">
      <div class="partner__mark"></div>
      <div class="partner__name">Amber Ledge Partners</div>
    </div>
  </section>

  <section class="card card--back" aria-label="Card back">
    <svg class="wave" viewBox="0 0 620 354" preserveAspectRatio="none" aria-hidden="true">
      <path class="stripe" transform="translate(0,-16)" d="M0,330 C220,326 360,304 440,234 C500,182 540,154 620,150 L620,370 L0,370 Z"/>
      <path class="gap" transform="translate(0,-7)" d="M0,330 C220,326 360,304 440,234 C500,182 540,154 620,150 L620,370 L0,370 Z"/>
      <path class="band" d="M0,330 C220,326 360,304 440,234 C500,182 540,154 620,150 L620,354 L0,354 Z"/>
    </svg>
    <div class="brand">
      <span class="brand__dot"></span>
      <div>
        <div class="brand__name">BrightHarborTrade.example</div>
        <div class="brand__tagline">Activities-Dining-Health-Beauty</div>
      </div>
    </div>
    <div class="contact">
      <div class="contact__name">DARA QUILL</div>
      <div class="contact__role">President</div>
      <div class="contact__line">4870 West 63rd Avenue, Suite C207</div>
      <div class="contact__line">Phoenix AZ 85731</div>
      <div class="contact__row">
        <svg viewBox="0 0 12 12"><path d="M2 1.5 L4.5 1.5 L5.2 4 L3.8 5 C4.5 6.6 5.4 7.5 7 8.2 L8 6.8 L10.5 7.5 L10.5 10 C6 10.5 1.5 6 2 1.5 Z"/></svg>
        <span>555-014-2287</span>
      </div>
      <div class="contact__row">
        <svg viewBox="0 0 12 12"><rect x="1" y="2.5" width="10" height="7"/><path d="M1 2.5 L6 6.5 L11 2.5"/></svg>
        <span>dara@brightharbortrade.example</span>
      </div>
    </div>
    <div class="web">www.brightharbortrade.example</div>
  </section>

</main>
</body>
</html>
```